Zvo Klinieken website for a maxillofacial surgery clinic

It's a website for a clinic for maxillofacial surgery in WordPress . The website doesn't need to be complicated but has to look professional. It needs to be in Dutch so i can give the texts. Similar websites are www.tandartsenpraktijkveldorm.nl or www.pbtspecialisten.nl. Pages would be sort of similar to https://hetcentrumvoorgezichtszorg.nl/ or https://wervelmondclinics.nl/. Those lasts are maxillofacial surgery clinic websites, but there are little more extensive.
I uploaded the logo. If this is not the proper quality i can upload the eps. Logo was made through pixelforum.

Target Market(s)

Patients who can find me and see information about the clinic

Industry/Entity Type

Healthcare

Coding

Coded - Design and coding required

Number of Pages Required

5+ page

Font styles to use
Other font styles liked:
• Something standard professional

Colors
0054AA
0677BA
7BADD7
CADEEF
E8F1F8

Requirements
Nice to have
• Something in line with the logo. I prefer a little dark like the darker logos but I'm not sure if that's professional. Logos bkvzo and rlpw are instances i'm registered to so they will have to be on the website too but small somewhere.

```html
<!DOCTYPE html>
<html lang="nl">
<head>
<meta charset="utf-8">
<title>Zvo Klinieken – Kaakchirurgie</title>
<link rel="stylesheet" href="https://fonts.googleapis.com/css2?family=Ubuntu:wght@400;500;700&family=Lato:wght@400;700;900&display=swap">
<style>
:root{
  --primary:#1f9fe3;
  --navy:#13294b;
  --footer:#0f1d30;
  --heading:#2b3f58;
  --text:#6d7682;
  --light:#f2f2f2;
  --pale:#e8f1f8;
  --line:#dfe5ea;
  --white:#fff;
}
*{box-sizing:border-box;margin:0;padding:0}
html,body{width:1200px;height:4967px;overflow:hidden}
body{position:relative;background:var(--white);font-family:'Lato',sans-serif;color:var(--text)}
.abs{position:absolute}
h1,h2,h3,h4{font-family:'Ubuntu',sans-serif;color:var(--heading);font-weight:500}
.eyebrow{font-size:11px;color:var(--primary);text-transform:uppercase;letter-spacing:.5px;display:flex;align-items:center;gap:10px}
.eyebrow .dash{width:48px;height:2px;background:var(--primary)}
.btn{position:absolute;display:flex;align-items:center;justify-content:center;font-family:'Lato',sans-serif;font-weight:900;font-size:13px;color:#fff;background:var(--primary);border-radius:4px}
.ph{position:absolute}

/* header */
.topbar{left:0;top:0;width:1200px;height:106px;background:#f4f4f4}
.logo{left:98px;top:22px;display:flex;align-items:center;gap:8px;font-family:'Ubuntu',sans-serif;font-weight:500;font-size:24px;color:var(--primary)}
.logo .mark{width:20px;height:20px;border-radius:50%;background:var(--primary)}
.info{display:flex;gap:14px;align-items:center;top:22px}
.info small{display:block;font-size:10px;color:#333;text-transform:uppercase;letter-spacing:.3px}
.info span{font-size:11px;color:#333}
.divider{left:651px;top:20px;width:1px;height:48px;background:#bbb}
.cta-top{left:945px;top:19px;width:168px;height:48px;background:var(--navy);font-size:12px}
.nav{left:85px;top:77px;width:1028px;height:68px;background:#fff;border-radius:4px;box-shadow:0 4px 14px rgba(0,0,0,.08);display:flex;align-items:center;padding-left:36px;gap:45px;font-size:14px;color:#444;z-index:3}
.social{right:30px;top:14px;display:flex;gap:12px}
.social i{display:block;width:36px;height:36px;border-radius:3px}

/* hero */
.hero{left:0;top:106px;width:1200px;height:687px;background:linear-gradient(110deg,#3a3c40 0%,#5d5450 40%,#48494d 70%,#2e3136 100%)}
.hero-tag{left:511px;top:331px;width:162px;height:36px;background:#2f3c54;color:#fff;font-size:12px;font-weight:700;display:flex;align-items:center;justify-content:center;border-radius:3px}
.hero-title{left:0;top:380px;width:1200px;text-align:center;font-family:'Ubuntu',sans-serif;font-weight:700;font-size:62px;line-height:74px;color:#fff}
.hero-btn{left:507px;top:547px;width:170px;height:48px;border:1.5px solid #fff;background:transparent;font-size:12px}
.arrow-box{width:62px;height:62px;background:#fff;border-radius:3px;display:flex;align-items:center;justify-content:center}

/* about */
.about-photo{left:96px;top:921px;width:444px;height:434px;border-radius:50%;background:linear-gradient(135deg,#3d4e6e,#c9d4e1 55%,#e9e3dc);border-left:10px solid #2f3e5c}
.tooth{left:436px;top:1245px;width:100px;height:100px;border-radius:50%;background:#fff;box-shadow:0 6px 18px rgba(0,0,0,.12);display:flex;align-items:center;justify-content:center}
.about-text{left:612px;top:940px;width:480px}
.about-text h2{font-size:47px;line-height:64px;margin-top:22px}
.about-text p{font-size:12.5px;line-height:24.5px;margin-top:22px;color:#777}

/* services */
.services{left:0;top:1460px;width:1200px;height:820px;background:var(--light)}
.svc-card{top:1682px;width:320px;height:313px;border-radius:4px;overflow:hidden}
.svc-card .ph{inset:0}
.svc-card .shade{position:absolute;inset:0;background:linear-gradient(180deg,rgba(15,30,55,.35),rgba(15,30,55,.6))}
.svc-icon{position:absolute;left:42px;top:46px;width:64px;height:64px;background:#fff;border-radius:6px;display:flex;align-items:center;justify-content:center}
.svc-card h3{position:absolute;left:34px;top:150px;color:#fff;font-size:23px}
.svc-card p{position:absolute;left:34px;top:212px;color:#fff;font-size:13px}
.svc-card .more{position:absolute;left:34px;top:248px;color:#fff;font-weight:700;font-size:15px}
.svc-card .bar{position:absolute;left:34px;top:275px;width:250px;height:2px;background:var(--primary)}
.sq-arrow{width:46px;height:64px;background:#fff;display:flex;align-items:center;justify-content:center;box-shadow:0 2px 8px rgba(0,0,0,.08)}

/* banner */
.banner{left:95px;top:2178px;width:1016px;height:208px;border-radius:8px;background:linear-gradient(90deg,#1d3159 0%,#2a4a7e 45%,#3a63a0 100%)}
.banner h3{position:absolute;left:36px;top:90px;color:#fff;font-size:23px;font-weight:700}
.quote{left:588px;top:85px;width:166px;height:52px;border:1.5px solid #fff;color:#fff;font-weight:700;font-size:14px;display:flex;align-items:center;justify-content:center}
.phone-btn{left:760px;top:85px;width:204px;height:52px;background:#fff;color:#222;font-size:15px;display:flex;align-items:center;justify-content:center;gap:12px}

/* why */
.center-head{left:0;width:1200px;text-align:center}
.center-head .eyebrow{justify-content:center}
.center-head h2{font-size:47px;margin-top:14px}
.portrait{left:434px;top:2576px;width:328px;height:366px;border-radius:0 0 164px 164px}
.portrait .ph{left:0;top:38px;width:328px;height:328px;border-radius:50%;background:linear-gradient(160deg,#3e4f80,#2c3b66 60%,#7a8699)}
.portrait .head{left:104px;top:0;width:120px;height:150px;border-radius:60px 60px 40px 40px;background:#6d5d55}
.feat{width:240px}
.feat h4{font-size:20px;font-weight:400}
.feat p{font-size:12.5px;line-height:18px;margin-top:6px;color:#888}
.feat.l{text-align:center}
.ficon{width:80px;height:80px;border-radius:50%;background:#fff;box-shadow:0 4px 18px rgba(0,0,0,.1);display:flex;align-items:center;justify-content:center}

/* testimonials */
.testi-photo{left:0;top:3058px;width:338px;height:532px;background:linear-gradient(160deg,#2d4270,#4a5e86 50%,#2a3c63)}
.testi-bg{left:338px;top:3058px;width:862px;height:532px;background:var(--light)}
.tcard{top:3256px;width:347px;height:208px;background:#fff;border-radius:4px;box-shadow:0 2px 10px rgba(0,0,0,.06);padding:32px 24px 0 24px}
.tcard p{font-size:12.5px;line-height:23px;color:#888}
.author{position:absolute;left:24px;bottom:24px;display:flex;align-items:center;gap:12px;font-size:12px;font-weight:700;color:#222}
.author i{display:block;width:50px;height:50px;border-radius:50%;background:linear-gradient(135deg,#8a9bb0,#546377)}
.qmark{position:absolute;right:28px;bottom:42px;font-family:'Ubuntu',sans-serif;font-weight:700;font-size:44px;color:#222;line-height:20px}
.dots{left:632px;top:3505px;display:flex;gap:21px;align-items:center}
.dots i{display:block;width:6px;height:6px;border-radius:50%;background:#9aa}
.dots i.on{width:14px;height:14px;border:2px solid var(--primary);background:radial-gradient(var(--primary) 35%,transparent 40%)}

/* contact */
.ccard{left:89px;top:3845px;width:1020px;height:414px;background:#fff;box-shadow:0 4px 20px rgba(0,0,0,.08)}
.cphoto{left:0;top:0;width:422px;height:414px;background:linear-gradient(160deg,#dfe6ed,#c6d3e0 45%,#1e5a93 70%,#e6ecf1)}
.ctel{left:194px;top:316px;width:196px;height:52px;background:#fff;display:flex;align-items:center;justify-content:center;gap:12px;font-size:16px;color:#222}
.cform h3{font-size:22px;font-weight:500;color:#333}
.cform p{font-size:13px;line-height:22px;color:#999;margin-top:8px;width:490px}
.field{position:absolute;height:46px;border:1px solid #d5d5d5;border-radius:3px;font-size:12px;color:#999;padding:16px 16px 0}
.send{left:465px;top:306px;width:501px;height:47px;font-size:11px;gap:8px}

/* footer */
.footer{left:0;top:4404px;width:1200px;height:505px;background:var(--footer)}
.strip{left:118px;top:4378px;width:964px;height:26px;background:var(--pale);clip-path:polygon(0 100%,1% 0,100% 40%,100% 100%)}
.reach{left:85px;top:4404px;width:1030px;height:154px;background:#fff;display:flex}
.reach div{flex:1;display:flex;flex-direction:column;align-items:center;justify-content:center;gap:16px;font-size:15px;font-weight:700;color:#333;border-right:1px solid #e7e7e7}
.reach div:last-child{border-right:none}
.fcol{top:4610px;color:#c5ccd6;font-size:13px;line-height:22px}
.fcol h4{font-family:'Lato',sans-serif;font-weight:700;color:#fff;font-size:16px;margin-bottom:38px}
.links{display:grid;grid-template-columns:170px 120px;row-gap:12px;font-size:13px;color:#c5ccd6}
.sub{display:flex;margin-top:24px;border-bottom:1px solid #fff;width:306px;height:44px}
.sub span{flex:1;font-size:11px;padding:16px 10px 0;color:#aab}
.sub b{width:104px;border-left:1px solid #fff;border-top:1px solid #fff;border-right:1px solid #fff;color:var(--primary);font-size:13px;display:flex;align-items:center;justify-content:center}
.bottom{left:0;top:4909px;width:1200px;height:58px;background:var(--pale)}
.bottom strong{position:absolute;left:87px;top:22px;font-size:12px;color:#222}
.fsoc{position:absolute;right:74px;top:24px;display:flex;gap:28px}
.fsoc i{display:block;width:10px;height:10px;border-radius:2px;background:#1f2a3a}
.totop{left:1138px;top:4899px;width:48px;height:48px;background:var(--primary);border-radius:4px;display:flex;align-items:center;justify-content:center}
</style>
</head>
<body>

<!-- Header -->
<header>
  <div class="abs topbar"></div>
  <div class="abs logo"><span class="mark"></span>Zvo Klinieken</div>
  <div class="abs info" style="left:428px">
    <svg width="30" height="30" viewBox="0 0 24 24" fill="none" stroke="#1b2a44" stroke-width="1.6"><path d="M12 22s7-7 7-12a7 7 0 1 0-14 0c0 5 7 12 7 12z"/><circle cx="12" cy="10" r="2.5"/></svg>
    <div><small>Location</small><span>45 Laan, Stad</span></div>
  </div>
  <div class="abs divider"></div>
  <div class="abs info" style="left:678px">
    <svg width="34" height="34" viewBox="0 0 24 24" fill="none" stroke="#1b2a44" stroke-width="1.6"><circle cx="12" cy="12" r="9"/><path d="M8 12h8M13 9l3 3-3 3"/></svg>
    <div><small>Office Hours</small><span>9.00 to 7.00 &nbsp;[Sun: Closed]</span></div>
  </div>
  <div class="btn cta-top">MAAK EEN AFSPRAAK</div>
  <nav class="abs nav">
    <span>Thuis</span><span>Behandelingen</span><span>Vergoeding</span><span>Ons team</span><span>Folders</span><span>Gallery</span><span>Contact Us</span>
    <div class="abs social">
      <i style="background:#3b5b9a" aria-label="Sociaal profiel 1"></i>
      <i style="background:#d92c2c" aria-label="Sociaal profiel 2"></i>
      <i style="background:#2ba3e6" aria-label="Sociaal profiel 3"></i>
    </div>
  </nav>
</header>

<!-- Hero -->
<section>
  <div class="abs hero" role="img" aria-label="Foto van een kaakchirurg die een patiënt behandelt, donker overlay"></div>
  <div class="abs hero-tag">KAAKCHIRURGIE</div>
  <h1 class="abs hero-title">Precisiechirurgie,<br>Persoonlijke Zorg</h1>
  <div class="btn hero-btn">MEER LEREN</div>
  <div class="abs arrow-box" style="left:43px;top:488px"><svg width="20" height="20" viewBox="0 0 24 24" fill="none" stroke="#1b2a44" stroke-width="2"><path d="M20 12H4M10 6l-6 6 6 6"/></svg></div>
  <div class="abs arrow-box" style="left:1094px;top:488px"><svg width="20" height="20" viewBox="0 0 24 24" fill="none" stroke="#1b2a44" stroke-width="2"><path d="M4 12h16M14 6l6 6-6 6"/></svg></div>
</section>

<!-- About -->
<section>
  <div class="abs about-photo" role="img" aria-label="Foto van een lachende patiënte tijdens een tandheelkundig onderzoek"></div>
  <div class="abs tooth"><svg width="56" height="56" viewBox="0 0 48 48" fill="none" stroke="#1f9fe3" stroke-width="2.2"><path d="M15 7c-6 0-9 5-8 11 1 5 3 8 4 14 1 6 2 10 5 10s3-9 8-9 5 9 8 9 4-4 5-10c1-6 3-9 4-14 1-6-2-11-8-11-4 0-6 2-9 2s-5-2-9-2z"/></svg></div>
  <div class="abs about-text">
    <div class="eyebrow">Over ons <span class="dash"></span></div>
    <h2>Levens Kracht Geven,<br>Een Gezicht per Keer</h2>
    <p>Lorem ipsum dolor sit amet, consectetur adipiscing elit, sed do eiusmo d tempor incididunt ut labore et dolore magna aliqua. Ut enim ad min im veniam, quis nostrud exercitation ullamco laboris nisi ut aliquip ex ea commodo consequat. Duis aute irure dolor in reprehenderit in voluptate velit esse cillum dolore eu fugiat nulla pariatur. Excepteur sint occaecat cupidatat non proident, sunt in culpa qui officia deserunt mollit anim id est laborum.</p>
  </div>
  <div class="btn" style="left:612px;top:1296px;width:167px;height:44px">Meer Leren</div>
</section>

<!-- Services -->
<section>
  <div class="abs services"></div>
  <div class="abs eyebrow" style="left:90px;top:1543px">Diensten <span class="dash"></span></div>
  <h2 class="abs" style="left:90px;top:1577px;font-size:46px">Onze Diensten</h2>
  <div class="abs sq-arrow" style="left:998px;top:1558px"><svg width="16" height="16" viewBox="0 0 24 24" fill="none" stroke="#111" stroke-width="3"><path d="M15 5l-7 7 7 7"/></svg></div>
  <div class="abs sq-arrow" style="left:1050px;top:1558px"><svg width="16" height="16" viewBox="0 0 24 24" fill="none" stroke="#111" stroke-width="3"><path d="M9 5l7 7-7 7"/></svg></div>

  <article class="abs svc-card" style="left:93px">
    <div class="ph" role="img" aria-label="Foto van een chirurg met mondkapje tijdens een ingreep" style="background:linear-gradient(135deg,#5c6f8a,#9aa9bd 50%,#3f4f68)"></div>
    <div class="shade"></div>
    <div class="svc-icon"><svg width="38" height="38" viewBox="0 0 24 24" fill="none" stroke="#2b3f58" stroke-width="2" stroke-linecap="round"><path d="M12 3v3M12 18v3M3 12h3M18 12h3M5.6 5.6l2.1 2.1M16.3 16.3l2.1 2.1M5.6 18.4l2.1-2.1M16.3 7.7l2.1-2.1"/></svg></div>
    <h3>Kaakchirurgie</h3><p>Lorem ipsum dolor sit amet, consectetur</p><span class="more">Meer Leren</span><i class="bar"></i>
  </article>
  <article class="abs svc-card" style="left:440px">
    <div class="ph" role="img" aria-label="Foto van een glimlachende vrouw" style="background:linear-gradient(135deg,#7a6a5e,#c79c72 50%,#5a4d45)"></div>
    <div class="shade"></div>
    <div class="svc-icon"><svg width="38" height="38" viewBox="0 0 24 24" fill="none" stroke="#2b3f58" stroke-width="2"><circle cx="12" cy="12" r="9"/><path d="M8 12h8M10 10l-2 2 2 2M14 10l2 2-2 2"/></svg></div>
    <h3>Slaapgeneeskunde</h3><p>Lorem ipsum dolor sit amet, consectetur</p><span class="more">Meer Leren</span><i class="bar"></i>
  </article>
  <article class="abs svc-card" style="left:787px">
    <div class="ph" role="img" aria-label="Foto van een lachend kind" style="background:linear-gradient(135deg,#8b98a8,#d3c2b0 50%,#6e7c8f)"></div>
    <div class="shade"></div>
    <div class="svc-icon"><svg width="38" height="38" viewBox="0 0 24 24" fill="none" stroke="#2b3f58" stroke-width="2"><path d="M4 7h16"/><circle cx="8" cy="14" r="3"/><circle cx="16" cy="14" r="3"/></svg></div>
    <h3>Plastische Chirurgie</h3><p>Lorem ipsum dolor sit amet, consectetur</p><span class="more">Meer Leren</span><i class="bar"></i>
  </article>
  <div class="btn" style="left:511px;top:2070px;width:168px;height:46px">Meer Leren</div>
</section>

<!-- Banner -->
<section class="abs banner" role="img" aria-label="Foto van een chirurgisch team met blauwe overlay">
  <h3>Symmetrie Vormgeven, Harmonie Herstellen</h3>
  <div class="abs quote">Get A Quote</div>
  <div class="abs phone-btn"><svg width="20" height="20" viewBox="0 0 24 24" fill="#111"><path d="M6.6 10.8a15 15 0 0 0 6.6 6.6l2.2-2.2c.3-.3.7-.4 1-.2 1.1.4 2.3.6 3.6.6.6 0 1 .4 1 1V20c0 .6-.4 1-1 1A17 17 0 0 1 3 4c0-.6.4-1 1-1h3.5c.6 0 1 .4 1 1 0 1.3.2 2.5.6 3.6.1.3 0 .7-.2 1z"/></svg>0890 - 555 - 0147</div>
</section>

<!-- Why -->
<section>
  <div class="abs center-head" style="top:2442px"><div class="eyebrow"><span class="dash"></span>Why chose us<span class="dash"></span></div><h2>Waarom Voor Ons Kiezen</h2></div>
  <div class="abs portrait">
    <div class="ph" role="img" aria-label="Foto van een lachende arts in pak"></div>
  </div>

  <div class="abs feat l" style="left:118px;top:2618px"><h4>Kwaliteitsborging</h4><p>Lorem ipsum dolor sit amet,<br>consectetur adipiscing elit</p></div>
  <div class="abs feat l" style="left:78px;top:2742px"><h4>Persoonlijke Aanpak</h4><p>Lorem ipsum dolor sit amet,<br>consectetur adipiscing elit</p></div>
  <div class="abs feat l" style="left:128px;top:2867px"><h4>Klantgericht</h4><p>Lorem ipsum dolor sit amet,<br>consectetur adipiscing elit</p></div>

  <div class="abs ficon" style="left:355px;top:2614px"><svg width="34" height="34" viewBox="0 0 24 24" fill="none" stroke="#1f9fe3" stroke-width="1.8"><circle cx="12" cy="4" r="2"/><path d="M4 8h16M12 8v6M8 21l4-7 4 7"/></svg></div>
  <div class="abs ficon" style="left:318px;top:2738px"><svg width="34" height="34" viewBox="0 0 24 24" fill="none" stroke="#1f9fe3" stroke-width="2" stroke-linecap="round"><path d="M12 3v3M12 18v3M3 12h3M18 12h3M5.6 5.6l2.1 2.1M16.3 16.3l2.1 2.1M5.6 18.4l2.1-2.1M16.3 7.7l2.1-2.1"/></svg></div>
  <div class="abs ficon" style="left:352px;top:2862px"><svg width="34" height="34" viewBox="0 0 24 24" fill="none" stroke="#1f9fe3" stroke-width="1.8"><path d="M4 13a8 8 0 0 1 16 0v4H4z"/><path d="M8 17v3M16 17v3"/></svg></div>

  <div class="abs ficon" style="left:762px;top:2614px"><svg width="34" height="34" viewBox="0 0 24 24" fill="none" stroke="#1f9fe3" stroke-width="1.6"><circle cx="12" cy="12" r="9"/><circle cx="12" cy="12" r="5"/><circle cx="12" cy="12" r="1.5"/></svg></div>
  <div class="abs ficon" style="left:796px;top:2738px"><svg width="34" height="34" viewBox="0 0 24 24" fill="none" stroke="#1f9fe3" stroke-width="1.8"><path d="M4 13a8 8 0 0 1 16 0v4H4z"/><path d="M8 17v3M16 17v3"/></svg></div>
  <div class="abs ficon" style="left:762px;top:2862px"><svg width="34" height="34" viewBox="0 0 24 24" fill="none" stroke="#1f9fe3" stroke-width="1.8"><rect x="3" y="3" width="5" height="5"/><rect x="16" y="3" width="5" height="5"/><rect x="3" y="16" width="5" height="5"/><rect x="16" y="16" width="5" height="5"/><path d="M8 5.5h8M5.5 8v8M18.5 8v8"/></svg></div>

  <div class="abs feat" style="left:892px;top:2618px"><h4>Bewezen Track Record</h4><p>Lorem ipsum dolor sit amet,<br>consectetur adipiscing elit</p></div>
  <div class="abs feat" style="left:900px;top:2742px"><h4>Professioneel</h4><p>Lorem ipsum dolor sit amet,<br>consectetur adipiscing elit</p></div>
  <div class="abs feat" style="left:876px;top:2867px"><h4>Ervaring</h4><p>Lorem ipsum dolor sit amet,<br>consectetur adipiscing elit</p></div>
</section>

<!-- Testimonials -->
<section>
  <div class="abs testi-photo" role="img" aria-label="Foto van een patiënt in de behandelstoel met blauwe overlay"></div>
  <div class="abs testi-bg"></div>
  <div class="abs center-head" style="left:338px;width:662px;top:3116px"><div class="eyebrow"><span class="dash"></span>Getuigenissen<span class="dash"></span></div><h2>Wat Klanten Zeggen</h2></div>

  <div class="abs tcard" style="left:135px"><p>Lorem ipsum dolor sit amet, consectetur adipis por incididunt ut labore et dolore magna aliqu uis nostrud exercitation ullamco laboris nisi consequat. Duis aute irure dolor in reprehend</p><div class="author"><i></i>Joris Damen</div><span class="qmark">”</span></div>
  <div class="abs tcard" style="left:500px;border-bottom:3px solid #2b3f58"><p>Lorem ipsum dolor sit amet, consectetur adipis por incididunt ut labore et dolore magna aliqu uis nostrud exercitation ullamco laboris nisi consequat. Duis aute irure dolor in reprehend</p><div class="author"><i></i>Joris Damen</div><span class="qmark">”</span></div>
  <div class="abs tcard" style="left:870px;width:330px"><p>Lorem ipsum dolor sit amet, consectetur adipis por incididunt ut labore et dolore magna aliqu uis nostrud exercitation ullamco laboris nisi consequat. Duis aute irure dolor in reprehend</p><div class="author"><i></i>Joris Damen</div><span class="qmark">”</span></div>
  <div class="abs dots"><i class="on"></i><i></i><i></i><i></i></div>
</section>

<!-- Contact -->
<section>
  <div class="abs center-head" style="top:3711px"><div class="eyebrow"><span class="dash"></span>Contact us<span class="dash"></span></div><h2>Kom Met Ons In Contact</h2></div>
  <div class="abs ccard">
    <div class="ph cphoto" role="img" aria-label="Foto van een tandarts in blauw uniform in de behandelkamer"></div>
    <div class="abs ctel"><svg width="20" height="20" viewBox="0 0 24 24" fill="#111"><path d="M6.6 10.8a15 15 0 0 0 6.6 6.6l2.2-2.2c.3-.3.7-.4 1-.2 1.1.4 2.3.6 3.6.6.6 0 1 .4 1 1V20c0 .6-.4 1-1 1A17 17 0 0 1 3 4c0-.6.4-1 1-1h3.5c.6 0 1 .4 1 1 0 1.3.2 2.5.6 3.6.1.3 0 .7-.2 1z"/></svg>1800-555-019</div>
    <div class="abs cform" style="left:465px;top:58px"><h3>Ontvang vandaag gratis consultatie</h3><p>Get a free consultation from our experts, Our customer support team help you 24/7. Don't hesitate.</p></div>
    <div class="field" style="left:465px;top:167px;width:501px">Your Name</div>
    <div class="field" style="left:465px;top:237px;width:236px">Your Email</div>
    <div class="field" style="left:727px;top:237px;width:239px">Message</div>
    <div class="btn send">GET IN TOUCH <svg width="14" height="14" viewBox="0 0 24 24" fill="none" stroke="#fff" stroke-width="2.5"><path d="M4 12h16M14 6l6 6-6 6"/></svg></div>
  </div>
</section>

<!-- Footer -->
<footer>
  <div class="abs strip"></div>
  <div class="abs footer"></div>
  <div class="abs reach">
    <div><svg width="44" height="40" viewBox="0 0 24 24" fill="none" stroke="#1f9fe3" stroke-width="1.2"><path d="M12 15s5-5 5-8.5a5 5 0 1 0-10 0C7 10 12 15 12 15z"/><circle cx="12" cy="6.5" r="1.8"/><path d="M5 14l-3 7h20l-3-7"/></svg>Come to Our Location</div>
    <div><svg width="44" height="40" viewBox="0 0 24 24" fill="none" stroke="#1f9fe3" stroke-width="1.2"><rect x="3" y="6" width="18" height="14"/><path d="M3 6l9 7 9-7"/></svg>Send Us an Email</div>
    <div><svg width="44" height="40" viewBox="0 0 24 24" fill="none" stroke="#1f9fe3" stroke-width="1.2"><rect x="7" y="3" width="10" height="18" rx="2"/><path d="M11 18h2M19 9a4 4 0 0 1 0 6M21 7a7 7 0 0 1 0 10"/></svg>Give Us a Call</div>
  </div>

  <div class="abs fcol" style="left:85px;width:310px">
    <div style="display:flex;align-items:center;gap:8px;font-family:'Ubuntu',sans-serif;font-weight:500;font-size:28px;color:#4fb3ea;margin-bottom:26px"><span style="width:22px;height:22px;border-radius:50%;background:#4fb3ea;display:block"></span>Zvo Klinieken</div>
    <p>Lorem ipsum dolor sit amet, consectetur adipi por incididunt ut labore et dolore magna aliqu uis nostrud exercitation ullamco laboris nisi ut a consequat. Duis aute irure dolor in reprehend</p>
  </div>
  <div class="abs fcol" style="left:438px">
    <h4>Visit Our Place</h4>
    <p>18 Lindelaan<br>Appartement 3, 2511 AB</p>
    <p style="color:#fff;font-weight:700;font-size:11px;margin-top:10px">FIND US ON MAP</p>
    <div class="sub"><span>Enter Your Email...</span><b>SUBSCRIBE</b></div>
  </div>
  <div class="abs fcol" style="left:788px">
    <h4>Useful Links</h4>
    <div class="links"><span>About Us</span><span>Testimonials</span><span>Practice areas</span><span>FAQs</span><span>Why Choose Us</span><span>Cookies</span><span>How it works</span><span>Contact Us</span><span>News &amp; Updates</span><span>Privacy Policy</span></div>
  </div>

  <div class="abs bottom">
    <strong>Zvo Klinieken</strong>
    <div class="fsoc" aria-label="Sociale profielen"><i></i><i></i><i></i><i></i></div>
  </div>
  <div class="abs totop"><svg width="22" height="22" viewBox="0 0 24 24" fill="none" stroke="#fff" stroke-width="2.5"><path d="M5 15l7-7 7 7"/></svg></div>
</footer>

</body>
</html>
```